Modern Business Card

Modern professional business card with more than just logo and demographic info. Something memorable.

We are a trendy/modern chiropractic group with an emphasis on neurology, hence the minimalist-type brain logo. We want to convey that modern and technical aspect with professionalism and the elite nature of our practice environment.

```html
<!DOCTYPE html>
<html lang="en">
<head>
<meta charset="utf-8">
<title>Meridian Spine – Business Card</title>
<link rel="stylesheet" href="https://fonts.googleapis.com/css2?family=Open+Sans:wght@400;600;700&display=swap">
<style>
  :root {
    --brand-blue: #4681c1;
    --ink: #000000;
    --text-grey: #555555;
    --paper: #ffffff;
    --page: #ffffff;
  }
  * { margin: 0; padding: 0; box-sizing: border-box; }
  html, body {
    width: 1200px;
    height: 1200px;
    overflow: hidden;
    background: var(--page);
    font-family: "Open Sans", Arial, sans-serif;
  }
  .canvas { position: relative; width: 1200px; height: 1200px; }
  .card {
    position: absolute;
    left: 115px;
    width: 970px;
    height: 553px;
    box-shadow: 0 0 14px rgba(0, 0, 0, 0.10);
    overflow: hidden;
  }
  .card--front { top: 42px; background: var(--brand-blue); }
  .card--back { top: 605px; background: var(--paper); }

  .brand {
    display: flex;
    align-items: center;
    gap: 16px;
    font-weight: 600;
    letter-spacing: 2px;
    text-transform: uppercase;
    white-space: nowrap;
  }
  .brand__dot { border-radius: 50%; flex: none; }

  .card--front .brand {
    position: absolute;
    left: 0; right: 0; top: 240px;
    justify-content: center;
    color: var(--paper);
    font-size: 50px;
  }
  .card--front .brand__dot { width: 38px; height: 38px; background: var(--paper); }

  .card--back .brand {
    position: absolute;
    left: 102px; top: 114px;
    color: var(--brand-blue);
    font-size: 40px;
  }
  .card--back .brand__dot { width: 32px; height: 32px; background: var(--brand-blue); }

  .person {
    position: absolute;
    right: 575px;
    top: 338px;
    text-align: right;
  }
  .person__name { font-size: 34px; font-weight: 700; color: var(--ink); line-height: 1.2; }
  .person__role { font-size: 25px; font-weight: 400; color: var(--text-grey); line-height: 1.3; }

  .address {
    position: absolute;
    left: 515px; top: 276px;
    font-size: 26px;
    line-height: 35px;
    color: var(--text-grey);
    font-style: normal;
  }
  .contacts {
    position: absolute;
    left: 515px; top: 365px;
    list-style: none;
    font-size: 27px;
    color: var(--text-grey);
  }
  .contacts li { display: flex; align-items: center; height: 37px; }
  .contacts svg { width: 24px; height: 24px; margin-right: 18px; flex: none; }

  .footer-band {
    position: absolute;
    left: 0; bottom: 0;
    width: 100%;
    height: 48px;
    background: var(--brand-blue);
  }
</style>
</head>
<body>
<div class="canvas">

  <section class="card card--front">
    <div class="brand"><span class="brand__dot"></span>Meridian Spine</div>
  </section>

  <section class="card card--back">
    <div class="footer-band"></div>

    <div class="brand"><span class="brand__dot"></span>Meridian Spine</div>

    <div class="person">
      <p class="person__name">Daniel Reyes</p>
      <p class="person__role">President</p>
    </div>

    <address class="address">
      Street Name Here, Suite 100<br>
      Street Zip Code,Country
    </address>

    <ul class="contacts">
      <li>
        <svg viewBox="0 0 24 24" aria-hidden="true"><path fill="var(--brand-blue)" d="M6.6 10.8c1.4 2.8 3.8 5.1 6.6 6.6l2.2-2.2c.3-.3.7-.4 1-.2 1.1.4 2.3.6 3.6.6.6 0 1 .4 1 1V20c0 .6-.4 1-1 1C10.6 21 3 13.4 3 4c0-.6.4-1 1-1h3.5c.6 0 1 .4 1 1 0 1.3.2 2.5.6 3.6.1.3 0 .7-.2 1z"/></svg>
        01234-56789
      </li>
      <li>
        <svg viewBox="0 0 24 24" aria-hidden="true"><rect x="2" y="5" width="20" height="14" fill="var(--brand-blue)"/><path d="M2.5 5.5 12 13l9.5-7.5M2.5 18.5l7-6.5M21.5 18.5l-7-6.5" stroke="var(--paper)" stroke-width="1.5" fill="none"/></svg>
        info@yourwebsite.com
      </li>
      <li>
        <svg viewBox="0 0 24 24" aria-hidden="true"><g fill="none" stroke="var(--brand-blue)" stroke-width="1.8"><circle cx="12" cy="12" r="10"/><ellipse cx="12" cy="12" rx="4.5" ry="10"/><path d="M2 12h20M4 6.5h16M4 17.5h16"/></g></svg>
        www.yourwebsite.com
      </li>
    </ul>
  </section>

</div>
</body>
</html>
```